Local fast-growing company in the service sector

We are looking for a modern business card design, which should also appear on our letterheads

Target Market(s)

Private and industrial sectors

Contact Information for Business Card

Vorname Name
Kellberger Str. 18
73650 Winterbach
Tel.: 07146-839214-0
Name@agentur-kvtl.de

Colors
9d9d9d
919191
aaaaaa

Requirements
Must have
• The logo (file) in silver

```html
<!DOCTYPE html>
<html lang="de">
<head>
<meta charset="utf-8">
<title>KVTL Visitenkarte</title>
<link rel="stylesheet" href="https://fonts.googleapis.com/css2?family=Arimo:wght@400;700&display=swap">
<style>
  :root {
    --backdrop: #2b2b2b;
    --card-top: #ffffff;
    --card-bottom: #e9e9e9;
    --silver: #9d9d9d;
    --silver-mid: #919191;
    --silver-light: #aaaaaa;
    --ink: #3a3a3a;
    --rule: #555555;
  }
  * { box-sizing: border-box; margin: 0; padding: 0; }
  html, body { width: 1200px; height: 997px; overflow: hidden; }
  body {
    background: var(--backdrop);
    font-family: "Arimo", Arial, sans-serif;
    position: relative;
  }
  .business-card {
    position: absolute;
    left: 180px;
    top: 258px;
    width: 840px;
    height: 480px;
    background: linear-gradient(160deg, var(--card-top), var(--card-bottom));
    overflow: hidden;
    box-shadow: 0 12px 30px rgba(0,0,0,.45);
  }
  .edge-tab {
    position: absolute;
    width: 26px;
    height: 170px;
    background: linear-gradient(90deg, var(--silver-light), var(--silver));
    border-radius: 14px;
  }
  .edge-tab--left { left: -12px; top: 270px; }
  .edge-tab--right { right: -12px; top: 40px; }
  .brand {
    position: absolute;
    left: 250px;
    top: 70px;
    display: flex;
    align-items: center;
    gap: 18px;
  }
  .brand-mark {
    width: 62px;
    height: 62px;
    border-radius: 50%;
    background: var(--silver-mid);
  }
  .brand-text { display: flex; flex-direction: column; }
  .brand-name {
    font-size: 64px;
    font-weight: 700;
    color: var(--silver);
    line-height: 1;
    letter-spacing: 1px;
  }
  .brand-url {
    font-size: 20px;
    font-weight: 700;
    color: var(--silver);
    letter-spacing: 1.5px;
    margin-top: 4px;
  }
  .divider {
    position: absolute;
    left: 440px;
    top: 220px;
    width: 2px;
    height: 150px;
    background: linear-gradient(180deg, transparent, var(--rule) 30%, var(--rule) 70%, transparent);
  }
  .person {
    position: absolute;
    right: 440px;
    top: 290px;
    text-align: right;
    padding-right: 40px;
  }
  .person-name {
    font-size: 24px;
    font-weight: 700;
    color: var(--silver);
    letter-spacing: 1px;
    text-transform: uppercase;
  }
  .person-role {
    font-size: 16px;
    color: var(--ink);
    margin-top: 4px;
  }
  .contact {
    position: absolute;
    left: 480px;
    top: 225px;
    font-size: 16px;
    color: var(--ink);
    line-height: 1.35;
  }
  .contact-address { margin-bottom: 12px; }
  .contact-line {
    display: flex;
    align-items: center;
    gap: 14px;
    margin-bottom: 8px;
    color: var(--silver-mid);
  }
  .contact-icon {
    width: 22px;
    height: 22px;
    border-radius: 50%;
    background: var(--silver-mid);
    display: flex;
    align-items: center;
    justify-content: center;
  }
</style>
</head>
<body>
  <section class="business-card">
    <div class="edge-tab edge-tab--left"></div>
    <div class="edge-tab edge-tab--right"></div>

    <div class="brand">
      <div class="brand-mark"></div>
      <div class="brand-text">
        <span class="brand-name">KVTL</span>
        <span class="brand-url">agentur-kvtl.de</span>
      </div>
    </div>

    <div class="person">
      <p class="person-name">Jonas Albrecht</p>
      <p class="person-role">Managing Partner</p>
    </div>

    <div class="divider"></div>

    <div class="contact">
      <p class="contact-address">Kellberger Str. 18, 73650<br>Winterbach</p>
      <p class="contact-line">
        <span class="contact-icon">
          <svg width="12" height="12" viewBox="0 0 24 24" aria-hidden="true">
            <path fill="#fff" d="M6.6 10.8a15 15 0 0 0 6.6 6.6l2.2-2.2c.3-.3.7-.4 1-.2 1.1.4 2.3.6 3.6.6.6 0 1 .4 1 1V20c0 .6-.4 1-1 1C10.6 21 3 13.4 3 4c0-.6.4-1 1-1h3.5c.6 0 1 .4 1 1 0 1.3.2 2.5.6 3.6.1.3 0 .7-.2 1z"/>
          </svg>
        </span>
        07146-839214-0
      </p>
      <p class="contact-line">
        <span class="contact-icon">
          <svg width="12" height="12" viewBox="0 0 24 24" aria-hidden="true">
            <path fill="#fff" d="M3 5h18v14H3z"/>
            <path fill="none" stroke="#919191" stroke-width="2" d="M3 5l9 7 9-7"/>
          </svg>
        </span>
        Name@agentur-kvtl.de
      </p>
    </div>
  </section>
</body>
</html>
```